Website Design for Employee Moral and Happiness Company

Looking for a clean website design that explains our features in a step by step manner so our visitors know exactly what our site does before logging in.

The site is called "Velrato". See logo design and video for a sample of style and an overview of what we do.

Target Market(s)

Business owners that are looking to retain employees.

Number of Pages Required

1 page

```html
<!DOCTYPE html>
<html lang="en">
<head>
<meta charset="utf-8">
<title>Velrato – Employee Happiness</title>
<link href="https://fonts.googleapis.com/css2?family=Poppins:wght@400;500;600;700;800&display=swap" rel="stylesheet">
<style>
:root{
  --orange:#f26a0c;
  --orange-soft:#fde6d4;
  --ink:#111111;
  --text:#333333;
  --white:#ffffff;
}
*{margin:0;padding:0;box-sizing:border-box}
html,body{width:1200px;height:4241px;overflow:hidden}
body{position:relative;background:var(--white);font-family:'Poppins',sans-serif;color:var(--text)}
.abs{position:absolute}
.btn{position:absolute;display:flex;align-items:center;justify-content:center;border-radius:30px;font-weight:700;font-size:15px;letter-spacing:.3px;text-transform:uppercase;color:var(--white)}
.btn-dark{background:var(--ink)}
.btn-orange{background:var(--orange)}
.h2{position:absolute;font-weight:800;font-size:44px;color:var(--ink);text-transform:uppercase;letter-spacing:-.5px;line-height:1;white-space:nowrap}
.para{position:absolute;font-size:18.5px;line-height:34px;color:var(--text);white-space:nowrap}

/* header */
.topbar{left:678px;top:0;width:522px;height:40px;background:var(--orange);border-bottom-left-radius:26px;color:var(--white);font-size:15px;display:flex;align-items:center;padding-left:55px;gap:18px}
.topbar span{display:flex;align-items:center;gap:8px}
.logo{left:79px;top:30px;font-size:38px;font-weight:700;color:var(--ink);display:flex;align-items:center;gap:10px}
.logo i{width:16px;height:16px;border-radius:50%;background:var(--orange);display:block}
.nav{left:428px;top:66px;display:flex;gap:27px;font-size:15px;font-weight:500;color:#444;text-transform:uppercase}
.nav .active{color:var(--orange);position:relative}
.nav .active:after{content:"•••";position:absolute;left:10px;top:16px;font-size:12px;letter-spacing:1px}
.login{left:933px;top:56px;width:152px;height:43px;border:2px solid #888;border-radius:24px;display:flex;align-items:center;justify-content:center;gap:6px;color:var(--orange);font-weight:700;font-size:15px}

/* hero */
.hero-kicker{left:79px;top:216px;font-size:31px;font-weight:500;color:var(--ink);display:flex;align-items:center;gap:14px;letter-spacing:1px}
.hero-kicker:after{content:"";width:102px;height:2px;background:var(--ink)}
.hero-title{left:78px;top:258px;font-size:76px;font-weight:800;color:var(--orange);letter-spacing:-1px;line-height:1}
.hero-text{left:79px;top:338px;font-size:19.5px;line-height:34px;color:var(--ink)}
.badge{left:815px;top:165px;width:250px;height:70px;background:var(--white);border-radius:36px;display:flex;align-items:center;padding-left:24px;gap:12px;box-shadow:0 4px 14px rgba(0,0,0,.08)}
.badge i{width:38px;height:38px;border-radius:50%;background:var(--orange);display:block}
.badge div{font-size:17px;font-weight:600;line-height:20px;color:var(--ink);border-left:2px solid #ccc;padding-left:12px}
.badge b{color:var(--orange);font-weight:700;font-size:19px}
.slide-arrow{top:268px;width:33px;height:72px;background:#6d6d6d;display:flex;align-items:center;justify-content:center}

/* features */
.feat-title{left:0;width:1200px;top:1436px;text-align:center;font-size:44px;font-weight:800;color:var(--white);text-transform:uppercase}
.feat-sub{left:0;width:1200px;top:1495px;text-align:center;font-size:18.5px;line-height:34px;color:var(--white)}
.feature{position:absolute;width:330px;color:var(--white)}
.feature .ico{width:88px;height:88px;border-radius:50%;background:var(--white);display:flex;align-items:center;justify-content:center}
.feature h3{font-size:18.5px;font-weight:700;text-transform:uppercase;margin-top:12px}
.feature p{font-size:18.5px;line-height:34px;margin-top:4px}

/* why */
.adv-head{left:635px;top:2955px;font-size:18.5px;font-weight:700;color:#333}
.adv-list{left:635px;top:2990px;list-style:none;font-size:18.5px;color:#333}
.adv-list li{display:flex;align-items:center;gap:10px;height:43px}
.adv-list li i{width:16px;height:16px;border-radius:50%;background:var(--orange);display:flex;align-items:center;justify-content:center}

/* contact */
.contact{left:0;top:3280px;width:1200px;height:580px;background:linear-gradient(135deg,#2a2a2a,#141414)}
.contact-title{left:0;width:1200px;top:3352px;text-align:center;font-size:44px;font-weight:800;color:var(--white)}
.contact-sub{left:0;width:1200px;top:3410px;text-align:center;font-size:18.5px;line-height:34px;color:var(--white)}
.field{position:absolute;background:var(--white);border-radius:3px;font-size:15px;color:#555;padding:12px 18px}

/* footer */
.f-head{position:absolute;top:3925px;font-size:20px;font-weight:800;color:var(--ink);text-transform:uppercase}
.f-list{position:absolute;top:3968px;list-style:none;font-size:17px;color:#333;line-height:34px}
.f-text{left:79px;top:3968px;font-size:17px;line-height:34px;color:#333;white-space:nowrap}
.social{position:absolute;top:4082px;width:46px;height:46px;border:2px solid var(--orange);border-radius:8px}
.info-ico{position:absolute;left:890px;width:47px;height:47px;border-radius:8px;background:var(--orange);display:flex;align-items:center;justify-content:center}
.info-txt{position:absolute;left:962px;font-size:17px;line-height:27px;color:#333}
</style>
</head>
<body>

<!-- HEADER -->
<div class="abs topbar">
  <span><svg width="15" height="15" viewBox="0 0 24 24"><path fill="#fff" d="M6.6 10.8a15.1 15.1 0 0 0 6.6 6.6l2.2-2.2c.3-.3.7-.4 1-.2 1.1.4 2.3.6 3.6.6.6 0 1 .4 1 1V20c0 .6-.4 1-1 1A17 17 0 0 1 3 4c0-.6.4-1 1-1h3.5c.6 0 1 .4 1 1 0 1.3.2 2.5.6 3.6.1.3 0 .7-.2 1z"/></svg>248-317-5096</span>
  <span style="opacity:.7">|</span>
  <span><svg width="16" height="14" viewBox="0 0 24 20"><path fill="#fff" d="M2 0h20a2 2 0 0 1 2 2v16a2 2 0 0 1-2 2H2a2 2 0 0 1-2-2V2a2 2 0 0 1 2-2zm10 11 10-7V2L12 9 2 2v2z"/></svg>info@velrato.com</span>
</div>
<div class="abs logo">Velrato<i></i></div>
<nav class="abs nav">
  <span class="active">Home</span><span>About Us</span><span>Our Features</span><span>Blog</span><span>Contact</span>
</nav>
<div class="abs login"><svg width="14" height="16" viewBox="0 0 14 16"><circle cx="7" cy="4.5" r="3.5" fill="none" stroke="#f26a0c" stroke-width="1.6"/><path d="M1 15.5a6 6 0 0 1 12 0" fill="none" stroke="#f26a0c" stroke-width="1.6"/></svg>| LOG IN</div>

<!-- HERO -->
<svg class="abs" style="left:0;top:0" width="1200" height="780" viewBox="0 0 1200 780">
  <defs>
    <linearGradient id="heroPhoto" x1="0" y1="0" x2="1" y2="1">
      <stop offset="0" stop-color="#f1efeb"/><stop offset=".55" stop-color="#ddd6cc"/><stop offset="1" stop-color="#c9c2b8"/>
    </linearGradient>
  </defs>
  <path d="M80,585 Q600,900 1120,585 L1120,560 Q600,800 80,560 Z" fill="#f26a0c"/>
  <circle cx="599" cy="732" r="37" fill="#f26a0c"/>
  <path d="M599,718 V746 M591,738 L599,746 L607,738" stroke="#fff" stroke-width="2" fill="none"/>
  <path d="M0,112 H1200 V543 Q600,833 0,543 Z" fill="url(#heroPhoto)" role="img" aria-label="Photo of a smiling businesswoman working on a laptop at a desk"/>
</svg>
<div class="abs slide-arrow" style="left:0"><svg width="10" height="14"><path d="M8 1 2 7l6 6" stroke="#fff" stroke-width="2" fill="none"/></svg></div>
<div class="abs slide-arrow" style="left:1167px"><svg width="10" height="14"><path d="M2 1l6 6-6 6" stroke="#fff" stroke-width="2" fill="none"/></svg></div>
<div class="abs hero-kicker">To Help Business</div>
<div class="abs hero-title">LIKE YOURS</div>
<div class="abs hero-text">Lorem ipsum dolor sit amet consectetuo<br>nun adipis elitsed do eiusmod tempor</div>
<div class="btn btn-dark" style="left:79px;top:426px;width:214px;height:53px">Contact Us</div>
<div class="abs badge"><i></i><div>EMPLOYEE<br><b>HAPPINESS</b></div></div>

<!-- ABOUT -->
<svg class="abs" style="left:60px;top:800px" width="540" height="520" viewBox="0 0 540 520">
  <defs>
  <radialGradient id="aboutHalo" cx=".5" cy=".5" r=".5"><stop offset=".85" stop-color="#fde6d4"/><stop offset="1" stop-color="#fde6d4" stop-opacity="0"/></radialGradient>
  <linearGradient id="aboutPhoto" x1="0" y1="0" x2="1" y2="1"><stop offset="0" stop-color="#e6e8ea"/><stop offset="1" stop-color="#9a9c9e"/></linearGradient></defs>
  <circle cx="269" cy="253" r="245" fill="url(#aboutHalo)" role="img" aria-label="Soft orange halo decoration"/>
  <circle cx="269" cy="253" r="222" fill="#fff"/>
  <circle cx="269" cy="253" r="206" fill="url(#aboutPhoto)" role="img" aria-label="Photo of a smiling businessman in an office with a colleague on the phone behind him"/>
</svg>
<div class="h2" style="left:635px;top:898px">About Us</div>
<div class="para" style="left:635px;top:957px">Lorem ipsum dolor sit amet consectetur adipiscingi<br>elit sed do eiusmod tempor incididunt ut labore eto<br>dolore magna aliqua. Quis ipsum suspendisse des<br>ultrices gravida. Risus commodo viverra maecenas<br>accumsan lacus vel facilisis licius decorat.</div>
<div class="btn btn-orange" style="left:635px;top:1157px;width:188px;height:53px">About Us</div>

<!-- FEATURES -->
<svg class="abs" style="left:0;top:1360px" width="1200" height="860" viewBox="0 1360 1200 860">
  <defs><linearGradient id="featBg" x1="0" y1="0" x2="1" y2="1"><stop offset="0" stop-color="#f47a1c"/><stop offset="1" stop-color="#e45c02"/></linearGradient>
  <radialGradient id="mascot" cx=".5" cy=".45" r=".6"><stop offset="0" stop-color="#fff"/><stop offset=".6" stop-color="#fde3cc"/><stop offset="1" stop-color="#f28a3a"/></radialGradient></defs>
  <path d="M0,1530 Q600,1210 1200,1530 V2050 Q600,2360 0,2050 Z" fill="url(#featBg)" role="img" aria-label="Orange-tinted photo of a team meeting"/>
  <circle cx="597" cy="1816" r="194" fill="none" stroke="#fff" stroke-width="2"/>
  <circle cx="597" cy="1622" r="6" fill="#fff"/><circle cx="597" cy="2010" r="6" fill="#fff"/>
  <circle cx="403" cy="1816" r="6" fill="#fff"/><circle cx="791" cy="1816" r="6" fill="#fff"/>
  <circle cx="597" cy="1816" r="172" fill="none" stroke="#fff" stroke-width="4"/>
  <circle cx="597" cy="1816" r="160" fill="#e25a00"/>
  <circle cx="597" cy="1816" r="148" fill="url(#mascot)" role="img" aria-label="Brand mascot character"/>
</svg>
<div class="abs feat-title">Our Feature</div>
<div class="abs feat-sub">Lorem ipsum dolor sit amet consectetur adipiscingi<br>elit sed do eiusmod tempor incididunt ut labore</div>

<div class="feature" style="left:79px;top:1597px">
  <div class="ico"><svg width="50" height="34" viewBox="0 0 50 34"><path d="M2 17Q25-8 48 17Q25 42 2 17Z" fill="none" stroke="#f26a0c" stroke-width="2.5"/><circle cx="25" cy="17" r="8" fill="none" stroke="#f26a0c" stroke-width="2.5"/><circle cx="25" cy="17" r="3" fill="#f26a0c"/></svg></div>
  <h3>Clear Executive Vision</h3><p>dolore magna aliquat enim ad<br>minim veniam quis nostrud.</p>
</div>
<div class="feature" style="left:79px;top:1818px">
  <div class="ico"><svg width="50" height="36" viewBox="0 0 50 36"><circle cx="13" cy="22" r="10" fill="none" stroke="#f26a0c" stroke-width="2.5"/><circle cx="37" cy="22" r="10" fill="none" stroke="#f26a0c" stroke-width="2.5"/><path d="M6 14 11 3h7l3 10M44 14 39 3h-7l-3 10M21 16h8" fill="none" stroke="#f26a0c" stroke-width="2.5"/></svg></div>
  <h3>Employee Retention</h3><p>dolore magna aliquat enim ad<br>minim veniam quis nostrud.</p>
</div>
<div class="feature" style="left:828px;top:1597px">
  <div class="ico"><svg width="44" height="44" viewBox="0 0 44 44"><circle cx="22" cy="22" r="18" fill="none" stroke="#f26a0c" stroke-width="2.5"/><path d="M13 22l6 6 12-12" fill="none" stroke="#f26a0c" stroke-width="2.5"/></svg></div>
  <h3>Passion &amp; Impact</h3><p>dolore magna aliquat enim ad<br>minim veniam quis nostrud.</p>
</div>
<div class="feature" style="left:828px;top:1818px">
  <div class="ico"><svg width="46" height="44" viewBox="0 0 46 44"><rect x="3" y="7" width="40" height="34" rx="3" fill="none" stroke="#f26a0c" stroke-width="2.5"/><path d="M3 16h40M13 2v9M33 2v9" stroke="#f26a0c" stroke-width="2.5"/><path d="M23 21l2.6 5.2 5.7.8-4.1 4 1 5.7-5.2-2.7-5.1 2.7 1-5.7-4.2-4 5.7-.8z" fill="none" stroke="#f26a0c" stroke-width="2"/></svg></div>
  <h3>Event Planner</h3><p>dolore magna aliquat enim ad<br>minim veniam quis nostrud.</p>
</div>
<div class="btn btn-dark" style="left:459px;top:2066px;width:282px;height:52px">View More Features</div>

<!-- PROMISE -->
<div class="h2" style="left:81px;top:2340px">What We Promise</div>
<div class="para" style="left:81px;top:2397px">Lorem ipsum dolor sit amet consectetur adipiscingi<br>elit sed do eiusmod tempor incididunt ut labore eto<br>dolore magna aliqua. Quis ipsum suspendisse des<br>ultrices gravida. Risus commodo viverra maecenas<br>accumsan lacus vel facilisis licius decorat.</div>
<div class="btn btn-orange" style="left:81px;top:2597px;width:212px;height:53px">Contact Us</div>
<svg class="abs" style="left:590px;top:2305px" width="520" height="390" viewBox="590 2305 520 390">
  <defs><linearGradient id="teamPhoto" x1="0" y1="0" x2="1" y2="1"><stop offset="0" stop-color="#8a8682"/><stop offset=".5" stop-color="#d9d4cc"/><stop offset="1" stop-color="#6e6a66"/></linearGradient></defs>
  <path d="M1030,2360 H1103 V2610 A78,78 0 0 1 1025,2688 H968 V2620 H1030 Z" fill="#f26a0c"/>
  <path d="M640,2308 H1025 A53,53 0 0 1 1078,2361 V2590 A72,72 0 0 1 1006,2662 H665 A72,72 0 0 1 593,2590 V2355 A47,47 0 0 1 640,2308 Z" fill="url(#teamPhoto)" role="img" aria-label="Photo of a happy team doing a high five around a meeting table"/>
</svg>

<!-- WHY CHOOSE US -->
<svg class="abs" style="left:0;top:2765px" width="600" height="430" viewBox="0 2765 600 430">
  <defs>
  <linearGradient id="whyPhoto" x1="0" y1="0" x2="1" y2="1"><stop offset="0" stop-color="#f3f1ee"/><stop offset=".5" stop-color="#c8bfb4"/><stop offset="1" stop-color="#7b7168"/></linearGradient></defs>
  <rect x="5" y="2996" width="140" height="192" fill="#fde6d4" role="img" aria-label="Soft orange decorative block"/>
  <path d="M120,2770 H509 A80,80 0 0 1 589,2850 V3060 A94,94 0 0 1 495,3154 H120 A41,41 0 0 1 79,3113 V2811 A41,41 0 0 1 120,2770 Z" fill="url(#whyPhoto)" role="img" aria-label="Photo of colleagues smiling together around a laptop"/>
</svg>
<div class="h2" style="left:635px;top:2816px">Why Choose Us</div>
<div class="para" style="left:635px;top:2872px">Lorem ipsum dolor sit amet consectetur adipiscingi<br>elit sed do eiusmod tempor incididunt ut labore</div>
<div class="abs adv-head">ADVANTAGE</div>
<ul class="abs adv-list">
  <li><i><svg width="10" height="8"><path d="M1 4l3 3 5-6" stroke="#fff" stroke-width="1.8" fill="none"/></svg></i>Lorem ipsum dolor sit amet incididunt ut</li>
  <li><i><svg width="10" height="8"><path d="M1 4l3 3 5-6" stroke="#fff" stroke-width="1.8" fill="none"/></svg></i>Lorem ipsum dolor sit amet viverra sid</li>
  <li><i><svg width="10" height="8"><path d="M1 4l3 3 5-6" stroke="#fff" stroke-width="1.8" fill="none"/></svg></i>Risus commodo viverra maecenas</li>
</ul>

<!-- CONTACT -->
<div class="abs contact" role="img" aria-label="Dark photo of a business team in a meeting"></div>
<div class="abs contact-title">CONTACT US</div>
<div class="abs contact-sub">Lorem ipsum dolor sit amet consectetur adipiscingi<br>elit sed do eiusmod tempor incididunt ut labore</div>
<div class="field" style="left:245px;top:3522px;width:331px;height:50px">Enter Your Name</div>
<div class="field" style="left:245px;top:3588px;width:331px;height:51px">Email Address</div>
<div class="field" style="left:245px;top:3654px;width:331px;height:51px">Phone No</div>
<div class="field" style="left:593px;top:3522px;width:362px;height:183px">Leave your message !</div>
<div class="btn btn-orange" style="left:499px;top:3731px;width:202px;height:52px">Submit Now</div>

<!-- FOOTER -->
<div class="f-head" style="left:79px">About Us</div>
<div class="abs f-text">Lorem ipsum dolor sit amet consecter<br>adipiscingi elit sed do eiusmod tempor<br>incididunt ut labore vsiverra idm tote</div>
<div class="social" style="left:79px" aria-label="Social profile"></div>
<div class="social" style="left:135px" aria-label="Social profile"></div>
<div class="social" style="left:194px" aria-label="Social profile"></div>
<div class="abs" style="left:79px;top:4143px;font-size:17px;color:#333">Copyright © 2022 <span style="color:var(--orange)">Velrato.</span></div>

<div class="f-head" style="left:477px">Quick Links</div>
<ul class="f-list" style="left:477px"><li>Home</li><li>About Us</li><li>Our Features</li><li>Blog</li><li>Contact</li></ul>

<div class="f-head" style="left:675px">Others Link</div>
<ul class="f-list" style="left:675px"><li>Terms &amp; Condition</li><li>Privacy Policy</li><li>Cookie</li><li>Resister Now</li><li>User Login</li></ul>

<div class="f-head" style="left:890px">Contact Info</div>
<div class="info-ico" style="top:3975px"><svg width="18" height="18" viewBox="0 0 24 24"><path fill="#fff" d="M6.6 10.8a15.1 15.1 0 0 0 6.6 6.6l2.2-2.2c.3-.3.7-.4 1-.2 1.1.4 2.3.6 3.6.6.6 0 1 .4 1 1V20c0 .6-.4 1-1 1A17 17 0 0 1 3 4c0-.6.4-1 1-1h3.5c.6 0 1 .4 1 1 0 1.3.2 2.5.6 3.6.1.3 0 .7-.2 1z"/></svg></div>
<div class="info-txt" style="top:3970px">Phone:<br>248-317-5096</div>
<div class="info-ico" style="top:4038px"><svg width="18" height="16" viewBox="0 0 24 20"><path fill="#fff" d="M2 0h20a2 2 0 0 1 2 2v16a2 2 0 0 1-2 2H2a2 2 0 0 1-2-2V2a2 2 0 0 1 2-2zm10 11 10-7V2L12 9 2 2v2z"/></svg></div>
<div class="info-txt" style="top:4033px">Email:<br>contact@velrato.com</div>
<div class="abs" style="left:890px;top:4116px;font-size:17px;font-weight:500;color:var(--ink);border-bottom:2px solid var(--ink);display:flex;align-items:center;gap:8px">Find Us on Map <svg width="16" height="12"><path d="M0 6h14M9 1l5 5-5 5" stroke="#111" stroke-width="2" fill="none"/></svg></div>

</body>
</html>
```